Tandem Hearth Works Pty Ltd

We need business cards for a company based in Perth, we install, service and maintain fire equipment.
On the front we want a great design with our logo and a small spot for our full company name, general company email address and office number. On the back we need space for our name, title, mobile number and email address on the back.

Target Market(s)

Facility managers and commercial/industrial building owners/occupiers.

Contact Information for Business Card

Font styles to use
Sans Serif

Requirements
Must have
• Please only submit 5 of your best samples.
Darker tones are preferred.
Nice to have
• We want to use, black, red and grey. Keep it modern and clean.
I've attached the company logo and a sample of a boarder we use on our emergency plans.
Should not have
• No preference. Let the designer choose.

```html
<!DOCTYPE html>
<html lang="en">
<head>
<meta charset="utf-8">
<title>Tandem Hearth Works – Business Cards</title>
<link href="https://fonts.googleapis.com/css2?family=Montserrat:wght@400;500;600;800&display=swap" rel="stylesheet">
<style>
  :root {
    --backdrop: #3a3a3d;
    --card: #0d0d0e;
    --card-edge: #1a1a1c;
    --red: #ec1c24;
    --emboss: #1f1f21;
    --grey: #4a4a4d;
    --light: #e6e6e6;
  }
  * { margin: 0; padding: 0; box-sizing: border-box; }
  html, body { width: 1200px; height: 1200px; overflow: hidden; }
  body {
    background: var(--backdrop);
    font-family: 'Montserrat', sans-serif;
    display: flex;
    flex-direction: column;
    align-items: center;
    justify-content: center;
    gap: 60px;
  }
  .card {
    width: 700px;
    height: 400px;
    background: linear-gradient(160deg, var(--card-edge), var(--card) 55%);
    border-radius: 26px;
    position: relative;
    display: flex;
    flex-direction: column;
    align-items: center;
    justify-content: center;
    box-shadow: 0 18px 40px rgba(0,0,0,0.45);
  }
  .brand-name {
    font-weight: 800;
    font-size: 58px;
    letter-spacing: -1px;
    line-height: 1;
  }
  .card--front .brand-name { color: var(--emboss); }
  .card--back .brand-name { color: var(--red); }

  .company-line {
    margin-top: 70px;
    font-size: 15px;
    font-weight: 400;
    color: var(--grey);
    display: flex;
    align-items: center;
    gap: 8px;
  }
  .company-line .dot {
    width: 6px; height: 6px; border-radius: 50%; background: var(--red);
  }
  .contact-line {
    margin-top: 6px;
    font-size: 15px;
    color: var(--grey);
  }

  .card--back .brand-name { margin-top: -10px; }
  .person-name {
    margin-top: 42px;
    font-size: 22px;
    font-weight: 600;
    letter-spacing: 9px;
    color: var(--red);
  }
  .person-title {
    margin-top: 6px;
    font-size: 12px;
    font-weight: 500;
    letter-spacing: 3px;
    color: var(--light);
  }
  .contacts {
    margin-top: 28px;
    display: flex;
    flex-direction: column;
    align-items: center;
    gap: 8px;
    font-size: 16px;
    letter-spacing: 1.5px;
    color: var(--light);
  }
  .contact-row { display: flex; align-items: center; gap: 8px; }
  .contact-row svg { width: 14px; height: 14px; }
  .divider { color: var(--light); margin: 0 6px; }
  .accent { color: var(--red); }
</style>
</head>
<body>

  <section class="card card--front">
    <div class="brand-name">TANDEM HEARTH</div>
    <div class="company-line"><span class="dot"></span>Tandem Hearth Works Pty Ltd<span class="dot"></span></div>
    <div class="contact-line">123 456 7890 | youremail.com</div>
  </section>

  <section class="card card--back">
    <div class="brand-name">TANDEM HEARTH</div>
    <div class="person-name">MARCUS VALE</div>
    <div class="person-title">FOUNDER &amp; CEO</div>
    <div class="contacts">
      <div class="contact-row">
        <svg viewBox="0 0 24 24" aria-hidden="true"><path fill="#ec1c24" d="M6.6 10.8a15 15 0 0 0 6.6 6.6l2.2-2.2c.3-.3.7-.4 1-.2 1.1.4 2.3.6 3.6.6.6 0 1 .4 1 1V20c0 .6-.4 1-1 1A17 17 0 0 1 3 4c0-.6.4-1 1-1h3.5c.6 0 1 .4 1 1 0 1.3.2 2.5.6 3.6.1.3 0 .7-.2 1z"/></svg>
        <span>+61 400 555 019</span>
        <span class="divider">|</span>
        <svg viewBox="0 0 24 24" aria-hidden="true"><rect x="2" y="5" width="20" height="14" rx="1.5" fill="#ec1c24"/><path d="M3 6l9 7 9-7" fill="none" stroke="#0d0d0e" stroke-width="1.6"/></svg>
        <span>ceo@tandemhearth.com</span>
      </div>
      <div class="contact-row">
        <svg viewBox="0 0 24 24" aria-hidden="true"><circle cx="12" cy="12" r="9" fill="none" stroke="#ec1c24" stroke-width="2"/><path d="M3 12h18M12 3c3 3 3 15 0 18M12 3c-3 3-3 15 0 18" fill="none" stroke="#ec1c24" stroke-width="1.5"/></svg>
        <span>www.<span class="accent">tandemhearth</span>.com</span>
      </div>
    </div>
  </section>

</body>
</html>
```